Bright Harbor Counseling Letterhead for hip modern business

I would like some ombre use of the colors in the logo hip letterhead that incorporates logo colors and feel, needs to connect with young professionals and college students. i need to be able to write letters to schools to excuse absences as well. i like color blocks on one side preferably using colors from the attached logo design.

Target Market(s)

high income young people, young adults and college students

Industry/Entity Type

mental health

Font styles to use
Serif
Sans Serif

Colors
0054AA
0677BA
7BADD7
CADEEF
E8F1F8
0094D4
00A9DD
6FCCEA
C7EBF8
E9F6FB
00AB8E
00BBA5
67D7C9
C6EFE9
E9F9F6
59FF00
82FF00
B8FF75
E3FFCB
F4FFEA
A7469A
B969AE
D3A5CF
EDDBEB
F8F0F9
6B429C
8869AF
B7A5CE
E3DAEB
F3F0F8

Requirements
Must have
• a modern hip feel, somewhat color

```html
<!DOCTYPE html>
<html lang="en">
<head>
<meta charset="utf-8">
<title>Bright Harbor Counseling Letterhead</title>
<link rel="stylesheet" href="https://fonts.googleapis.com/css2?family=Quicksand:wght@400;500&family=Arimo:wght@400&display=swap">
<style>
  :root {
    --backdrop: #e9e7e4;
    --paper: #ffffff;
    --ink: #2f2f33;
    --body-ink: #56565c;
    --rule: #3a3a3a;
    --rule-soft: #9a9a9a;
    --band-magenta: #b9589f;
    --band-violet: #9169b2;
    --band-teal: #52c6bd;
    --accent-blue: #0677ba;
    --signature-wash: #f2f1f4;
  }
  * { box-sizing: border-box; margin: 0; padding: 0; }
  html, body { width: 1200px; height: 900px; overflow: hidden; }
  body { background: var(--backdrop); position: relative; }

  .letterhead {
    position: absolute; left: 266px; top: 20px;
    width: 668px; height: 860px;
    background: var(--paper);
    box-shadow: 0 2px 10px rgba(0,0,0,0.12);
    overflow: hidden;
  }
  .color-bands { position: absolute; left: 0; top: 0; width: 26px; height: 860px; }

  .brand {
    position: absolute; right: 80px; top: 72px;
    display: flex; align-items: center; gap: 8px;
  }
  .brand-dot { width: 14px; height: 14px; border-radius: 50%; background: var(--band-violet); }
  .brand-name {
    font-family: "Quicksand", sans-serif; font-weight: 400;
    font-size: 24px; letter-spacing: 0.5px; color: var(--ink);
  }
  .header-rule {
    position: absolute; left: 26px; top: 115px; width: 456px;
    border-top: 1px solid var(--rule);
  }

  .letter-title {
    position: absolute; left: 52px; top: 138px;
    font-family: "Quicksand", sans-serif; font-weight: 500;
    font-size: 24px; color: var(--ink);
  }
  .letter-body p {
    position: absolute; left: 52px; width: 588px;
    font-family: "Arimo", sans-serif; font-size: 9.6px; line-height: 13px;
    color: var(--body-ink); text-align: justify;
  }
  .p1 { top: 180px; } .p2 { top: 272px; } .p3 { top: 428px; }
  .p4 { top: 597px; } .p5 { top: 649px; }

  .signature-area {
    position: absolute; left: 402px; top: 712px; width: 238px; height: 54px;
    background: var(--signature-wash);
  }

  .contact-bar {
    position: absolute; left: 94px; top: 800px; width: 482px; height: 30px;
    border-top: 1px solid var(--rule-soft); border-bottom: 1px solid var(--rule-soft);
    display: flex; align-items: center; justify-content: center;
    font-family: "Quicksand", sans-serif; font-size: 11.5px; color: var(--body-ink);
  }
  .contact-item { display: flex; align-items: center; gap: 4px; padding: 0 10px; }
  .contact-item + .contact-item { border-left: 1.5px solid var(--band-teal); }
  .contact-icon { width: 10px; height: 10px; flex: none; }
</style>
</head>
<body>
  <main class="letterhead">
    <svg class="color-bands" viewBox="0 0 26 860" aria-hidden="true">
      <polygon points="0,0 26,0 26,210 0,196" fill="var(--band-magenta)"/>
      <polygon points="0,217 26,231 26,548 0,536" fill="var(--band-violet)"/>
      <polygon points="0,555 26,571 26,860 0,860" fill="var(--band-teal)"/>
    </svg>

    <header>
      <div class="brand">
        <span class="brand-dot"></span>
        <span class="brand-name">Bright Harbor Counseling</span>
      </div>
      <div class="header-rule"></div>
    </header>

    <h1 class="letter-title">Lorem ipsum</h1>

    <section class="letter-body">
      <p class="p1">Lorem ipsum dolor sit amet, consectetuer adipiscing elit, sed diam nonummy nibh euismod tincidunt ut laoreet dolore magna aliquam erat volutpat. Ut wisi enim ad minim veniam, quis nostrud exerci tation ullamcorper suscipit lobortis nisl ut aliquip ex ea commodo consequat. Duis autem vel eum iriure dolor in hendrerit in vulputate velit esse molestie consequat, vel illum dolore eu feugiat nulla facilisis at vero eros et accumsan et iusto odio dignissim qui blandit praesent luptatum zzril delenit augue duis dolore te feugait nulla facilisi.</p>
      <p class="p2">Lorem ipsum dolor sit amet, cons ectetuer adipiscing elit, sed diam nonummy nibh euismod tincidunt ut laoreet dolore magna aliquam erat volutpat. Ut wisi enim ad minim veniam, quis nostrud exerci tation ullamcorper suscipit lobortis nisl ut aliquip ex ea commodo consequat. Lorem ipsum dolor sit amet, consectetuer adipiscing elit, sed diam nonummy nibh euismod tincidunt ut laoreet dolore magna aliquam erat volutpat. Ut wisi enim ad minim veniam, quis nostrud exerci tation ullamcorper suscipit lobortis nisl ut aliquip ex ea commodo consequat. Duis autem vel eum iriure dolor in hendrerit in vulputate velit esse molestie consequat, vel illum dolore eu feugiat nulla facilisis at vero eros et accumsan et iusto odio dignissim qui blandit praesent luptatum zzril delenit augue duis dolore te feugait nulla facilisi.<br>Lorem ipsum dolor sit amet, cons ectetuer adipiscing elit, sed diam nonummy nibh euismod tincidunt ut laoreet dolore magna aliquam erat volutpat. Ut wisi enim ad minim veniam, quis nostrud exerci tation ullamcorper suscipit lobortis nisl ut aliquip ex ea commodo consequat.</p>
      <p class="p3">Lorem ipsum dolor sit amet, consectetuer adipiscing elit, sed diam nonummy nibh euismod tincidunt ut laoreet dolore magna aliquam erat volutpat. Ut wisi enim ad minim veniam, quis nostrud exerci tation ullamcorper suscipit lobortis nisl ut aliquip ex ea commodo consequat. Duis autem vel eum iriure dolor in hendrerit in vulputate velit esse molestie consequat, vel illum dolore eu feugiat nulla facilisis at vero eros et accumsan et iusto odio dignissim qui blandit praesent luptatum zzril delenit augue duis dolore te feugait nulla facilisi. Lorem ipsum dolor sit amet, cons ectetuer adipiscing elit, sed diam nonummy nibh euismod tincidunt ut laoreet dolore magna aliquam erat volutpat. Ut wisi enim ad minim veniam, quis nostrud exerci tation ullamcorper suscipit lobortis nisl ut aliquip ex ea commodo consequat. Lorem ipsum dolor sit amet, consectetuer adipiscing elit, sed diam nonummy nibh euismod tincidunt ut laoreet dolore magna aliquam erat volutpat. Ut wisi enim ad minim veniam, quis nostrud exerci tation ullamcorper suscipit lobortis nisl ut aliquip ex ea commodo consequat. Duis autem vel eum iriure dolor in hendrerit in vulputate velit esse molestie consequat, vel illum dolore eu feugiat nulla facilisis at vero eros et accumsan et iusto odio dignissim qui blandit praesent luptatum zzril delenit augue duis dolore te feugait nulla facilisi.</p>
      <p class="p4">Lorem ipsum dolor sit amet, cons ectetuer adipiscing elit, sed diam nonummy nibh euismod tincidunt ut laoreet dolore magna aliquam erat volutpat. Ut wisi enim ad minim veniam, quis nostrud exerci tation ullamcorper suscipit lobortis nisl ut aliquip ex ea commodo consequat.</p>
      <p class="p5">Lorem ipsum dolor sit amet, consectetuer adipiscing elit, sed diam nonummy nibh euismod tincidunt ut laoreet dolore magna aliquam erat volutpat. Ut wisi enim ad minim veniam, quis nostrud exerci tation ullamcorper suscipit lobortis nisl ut aliquip ex ea commodo consequat.</p>
    </section>

    <div class="signature-area" role="img" aria-label="Handwritten signature of the counselor"></div>

    <footer class="contact-bar">
      <span class="contact-item">
        <svg class="contact-icon" viewBox="0 0 10 10" aria-hidden="true"><circle cx="5" cy="5" r="5" fill="var(--accent-blue)"/><path d="M3.3 2.6c.3-.2.6-.1.7.2l.3.7c.1.2 0 .4-.2.5l-.3.2c.3.6.8 1.1 1.4 1.4l.2-.3c.1-.2.3-.3.5-.2l.7.3c.3.1.4.4.2.7-.4.6-1 .8-1.6.5C4.1 6.1 3.4 5.4 3 4.3c-.2-.6 0-1.3.3-1.7z" fill="#fff"/></svg>
        555-010-2040
      </span>
      <span class="contact-item">
        <svg class="contact-icon" viewBox="0 0 10 10" aria-hidden="true"><circle cx="5" cy="5" r="5" fill="var(--band-violet)"/><rect x="2.6" y="3.3" width="4.8" height="3.4" rx=".4" fill="#fff"/><path d="M2.8 3.5 5 5.2l2.2-1.7" stroke="var(--band-violet)" stroke-width=".6" fill="none"/></svg>
        hello@brightharbor.co
      </span>
      <span class="contact-item">
        <svg class="contact-icon" viewBox="0 0 10 10" aria-hidden="true"><circle cx="5" cy="5" r="5" fill="var(--band-magenta)"/><path d="M5 2.3a1.8 1.8 0 0 1 1.8 1.8C6.8 5.4 5 7.6 5 7.6S3.2 5.4 3.2 4.1A1.8 1.8 0 0 1 5 2.3z" fill="#fff"/><circle cx="5" cy="4.1" r=".6" fill="var(--band-magenta)"/></svg>
        Your address, your city, box 88900
      </span>
    </footer>
  </main>
</body>
</html>
```